A parent Company needs a website as a leading diversified business in industrial Conglomerates in Af

Velkor Group is a private (Holding) limited liability company incorporated under the Companies Code, 1963 (Act 179) in November, 2013 to following the speedy growth in numbers of its current subsidiaries which has been founded several years ago with an emerging force to become one of the largest and a leading diversified business in industrial Conglomerates in Africa.
The Group which is 100% wholly owned indigenous Ghanaian Company focuses on provision of local, value-added products and services that meet the needs of the African population. The Group is headquartered in Accra, Ghana with interests across a range of sectors in Africa.
We are currently into Food & Beverage, Real Estate Development, Transportation, Health Care, Consumer Products Distribution, Agro Processing, Manufacturing, ICT, Exports & Import, and still counting.
In the next 3 years, we shall announce our ambitions to enter Ghana's largest Oil and Gas industry, playing a strategic role in the petroleum sector with strategic alliances, and help build Ghana's biggest and most important Energy sector in the country.
Inspired by billionaires Tom Prewitt, Harlan Voskel, and Emeka Ofodile, Velkor Group (Velkor Foundation) is committed to making a name for itself on the philanthropic circuit and has given away privately and still given to the cause to the needy in the society and some specific social causes in Ghana.
The company is managed by a 5 member board and a 2 member advisory experts who are non-board members.
The company has a vision, mission and it is guided by its core values.
We would like to see a designs that is very professional and looks corporate and can attract investors and partners. It must communicate financial safety and growth and must reflect our logo colors.

```html
<!DOCTYPE html>
<html lang="en">
<head>
<meta charset="utf-8">
<title>Velkor Group</title>
<link rel="stylesheet" href="https://fonts.googleapis.com/css2?family=Ubuntu:wght@300;400;500&family=Open+Sans:wght@400;600&family=PT+Serif:ital@1&display=swap">
<style>
:root{
  --blue:#0aa3df;
  --red:#e3161d;
  --ink:#333;
  --muted:#8a8a8a;
  --line:#dcdcdc;
  --bg:#f7f7f7;
  --footer:#3d3d3d;
  --footer-deep:#333333;
  --footer-text:#c4c4c4;
}
*{box-sizing:border-box;margin:0;padding:0}
html,body{width:793px;height:1200px;overflow:hidden}
body{position:relative;background:var(--bg);font-family:"Open Sans",sans-serif;color:var(--ink)}
.abs{position:absolute}
.topbar{left:0;top:0;width:793px;height:3px;background:var(--blue)}
.brand{left:88px;top:22px;display:flex;align-items:center;gap:8px}
.brand-dot{width:30px;height:30px;border-radius:50%;background:var(--blue)}
.brand-name{font-family:"Ubuntu",sans-serif;font-size:16px;color:#2b2b2b;letter-spacing:.3px}
.nav{top:3px;left:385px;display:flex;height:79px;font-family:"Ubuntu",sans-serif;font-size:10px;color:#444}
.nav a{display:flex;align-items:center;padding:0 14px;text-decoration:none;color:inherit}
.nav a.active{background:#eef2f5;color:var(--red);font-weight:500;border-bottom:3px solid #cfe7f3;padding:0 17px}
.hero{left:0;top:82px;width:793px;height:317px;background:linear-gradient(180deg,#3b3f45 0%,#8a8d93 40%,#b6b8bc 70%,#5b5e63 100%)}
.hero-title{left:191px;top:211px;width:411px;height:52px;background:#1b1b1b;display:flex;align-items:center;justify-content:center;font-family:"Ubuntu",sans-serif;font-weight:300;font-size:27px;color:#fff}
.hero-title span{color:var(--red);margin-left:8px}
.dots{left:95px;top:348px;display:flex;gap:3px}
.dots i{width:8px;height:8px;border-radius:50%;background:var(--blue)}
.dots i:first-child{background:#fff;border:2px solid var(--blue)}
.service{top:447px;width:200px;height:93px;background:#fff;border:1px solid var(--line);text-align:center;padding-top:25px}
.service h3{font-family:"Ubuntu",sans-serif;font-weight:400;font-size:11px;letter-spacing:.2px;color:#222;margin-bottom:6px}
.service p{font-size:7.3px;line-height:12px;color:#444;padding:0 28px}
.service.active{background:var(--blue);border-color:var(--blue);box-shadow:3px 4px 6px rgba(0,0,0,.2)}
.service.active h3,.service.active p{color:#fff}
.badge{top:418px;width:40px;height:40px;border-radius:50%;background:var(--red);display:flex;align-items:center;justify-content:center}
.badge.blue{background:var(--blue);box-shadow:0 0 0 3px #fff}
.col-title{top:583px;width:193px;text-align:center;font-family:"Ubuntu",sans-serif;font-size:14px;color:#333}
.arrows{left:687px;top:586px}
.photo{top:611px;width:193px;height:115px;border:2px solid #fff;box-shadow:0 1px 2px rgba(0,0,0,.15)}
.caption{top:733px;width:193px;text-align:center;font-family:"Ubuntu",sans-serif;font-weight:500;font-size:10px}
.more{top:748px;width:193px;text-align:center;font-size:8px;color:var(--red);text-decoration:underline}
.more.blue{color:var(--blue)}
.rule{top:763px;width:193px;height:2px;background:#cfcfcf}
.rule.blue{background:var(--blue)}
.h2{font-family:"Ubuntu",sans-serif;font-size:14px;color:#333;display:flex;align-items:center;gap:10px}
.h2::after{content:"";flex:1;height:3px;border-top:1px solid var(--line);border-bottom:1px solid var(--line)}
.welcome{left:88px;top:794px;width:462px}
.body-text{font-size:7.8px;line-height:12.2px;color:var(--muted)}
.btn{left:87px;top:919px;width:59px;height:21px;background:var(--blue);color:#fff;font-size:8px;font-weight:600;display:flex;align-items:center;justify-content:center;border-radius:2px}
.testimonials{left:562px;top:794px;width:152px}
.avatar{left:565px;top:819px;width:37px;height:38px;background:linear-gradient(#e7e7e7,#8d8f94);border:1px solid #ccc}
.quote{left:565px;top:867px;width:150px;font-family:"PT Serif",serif;font-style:italic;font-size:8px;line-height:13.5px;color:var(--muted)}
.footer{left:0;top:971px;width:793px;height:189px;background:var(--footer)}
.footbar{left:0;top:1160px;width:793px;height:40px;background:var(--footer-deep);font-size:8px;color:#999}
.fh{font-family:"Ubuntu",sans-serif;font-size:10px;color:#e5e5e5;display:flex;align-items:center;gap:6px}
.fh::after{content:"";flex:1;border-top:1px solid #5a5a5a;border-bottom:1px solid #5a5a5a;height:3px}
.flist{font-size:7.5px;line-height:13.3px;color:var(--footer-text)}
.flist a{color:inherit;text-decoration:underline;display:block}
.social{left:529px;top:1034px;display:flex;gap:9px}
.social i{width:21px;height:21px;border-radius:2px;background:#3b5998}
.social i:nth-child(2){background:#4cb3e6}
.social i:nth-child(3){background:#1a7bb9}
.newsletter{left:528px;top:1091px;width:175px;height:22px;background:#2f2f2f;border:1px solid #2a2a2a;display:flex;align-items:center;justify-content:space-between;padding-left:8px}
.newsletter span{font-family:"PT Serif",serif;font-style:italic;font-size:7px;color:#777}
.newsletter b{background:var(--red);color:#fff;font-weight:400;font-size:8.5px;height:19px;width:55px;display:flex;align-items:center;justify-content:center;margin-right:1px;border-radius:2px}
.totop{left:377px;top:1131px;width:40px;height:40px;border-radius:50%;background:#555;display:flex;align-items:center;justify-content:center}
</style>
</head>
<body>
<div class="abs topbar"></div>
<div class="abs brand"><div class="brand-dot"></div><div class="brand-name">VELKOR GROUP</div></div>
<nav class="abs nav">
  <a class="active">Home</a><a>Food &amp; Beverage</a><a>Transportation</a><a>Health Care</a>
</nav>

<div class="abs hero" role="img" aria-label="Business team meeting around a conference table"></div>
<div class="abs hero-title">WELCOME TO<span>VELKOR GROUP</span></div>
<div class="abs dots"><i></i><i></i><i></i><i></i></div>

<div class="abs service" style="left:86px"><h3>FOOD &amp; BEVERAGES</h3><p>Sed ut perspiciatis unde omnis iste natus error sit voluptatem accusantium doloremque laudantium</p></div>
<div class="abs service active" style="left:297px"><h3>TRANSPORTATION</h3><p>Sed ut perspiciatis unde omnis iste natus error sit voluptatem accusantium doloremque laudantium</p></div>
<div class="abs service" style="left:508px"><h3>HEALTH &amp; CARE</h3><p>Sed ut perspiciatis unde omnis iste natus error sit voluptatem accusantium doloremque laudantium</p></div>

<div class="abs badge" style="left:166px">
  <svg width="18" height="20" viewBox="0 0 18 20" fill="#fff"><rect x="3" y="1" width="1.5" height="7"/><rect x="6" y="1" width="1.5" height="7"/><rect x="3" y="7" width="4.5" height="3" rx="1"/><rect x="4.3" y="9" width="2" height="10" rx="1"/><path d="M12 1c3 1 3 8 1 9v9h-2V1z"/></svg>
</div>
<div class="abs badge blue" style="left:377px">
  <svg width="24" height="16" viewBox="0 0 24 16" fill="#fff"><rect x="1" y="2" width="13" height="9"/><path d="M15 5h4l3 3v3h-7z"/><circle cx="5" cy="13" r="2"/><circle cx="18" cy="13" r="2"/></svg>
</div>
<div class="abs badge" style="left:588px">
  <svg width="20" height="20" viewBox="0 0 20 20" fill="none" stroke="#fff" stroke-width="1.6"><rect x="2" y="2" width="16" height="16" rx="2"/><path d="M3 10h4l2-4 2 8 2-5h4"/></svg>
</div>

<div class="abs col-title" style="left:87px">Our Vision</div>
<div class="abs col-title" style="left:301px">Our Mission</div>
<div class="abs col-title" style="left:515px">Our Partners</div>
<svg class="abs arrows" width="22" height="14" viewBox="0 0 22 14" fill="none" stroke-width="2"><path d="M7 1 1 7l6 6" stroke="#333"/><path d="M15 1l6 6-6 6" stroke="#e3161d"/></svg>

<div class="abs photo" style="left:87px;background:linear-gradient(135deg,#dfe4ea,#6b7787 55%,#c9cdd3)" role="img" aria-label="Smiling businessman holding a tablet in an office"></div>
<div class="abs photo" style="left:301px;background:radial-gradient(circle at 50% 60%,#6b4a2e,#c89a6e 45%,#f1ece4 80%)" role="img" aria-label="Hands holding soil with a young green seedling"></div>
<div class="abs photo" style="left:515px;background:linear-gradient(120deg,#2f3d52,#8796ab 50%,#dfe4ea)" role="img" aria-label="Two business partners shaking hands over a desk"></div>

<div class="abs caption" style="left:87px">Lorem Ipsum Dolor</div>
<div class="abs caption" style="left:301px">Lorem Ipsum Dolor</div>
<div class="abs caption" style="left:515px">Lorem Ipsum Dolor</div>
<div class="abs more" style="left:87px">Read More</div>
<div class="abs more blue" style="left:301px">Read More</div>
<div class="abs more" style="left:515px">Read More</div>
<div class="abs rule" style="left:88px"></div>
<div class="abs rule blue" style="left:301px"></div>
<div class="abs rule" style="left:515px"></div>

<section class="abs welcome">
  <h2 class="h2">Welcome To Velkor Group</h2>
  <p class="body-text" style="margin-top:7px">Lorem ipsum dolor sit amet, consectetur adipisicing elit, sed do eiusmod tempor incididunt ut labore et dolore magna aliqua. Ut enim ad minim veniam, quis nostrud exercitation ullamco laboris nisi ut aliquip ex ea commodo consequat. Duis aute irure dolor in reprehenderit in voluptate velit esse cillum dolore eu fugiat nulla pariatur. Excepteur sint occaecat cupidatat non proident, sunt in culpa qui officia deserunt mollit anim id est laborum.</p>
  <p class="body-text" style="margin-top:12px">Lorem ipsum dolor sit amet, consectetur adipisicing elit, sed do eiusmod tempor incididunt ut labore et dolore magna aliqua quis nostrud exercitation ullamco laboris nisi ut aliquip ex ea commodo consequat.</p>
</section>
<div class="abs btn">Read More</div>

<section class="abs testimonials"><h2 class="h2">Testimonials</h2></section>
<div class="abs avatar" role="img" aria-label="Portrait of the reviewer"></div>
<div class="abs" style="left:611px;top:819px">
  <div style="font-family:'Ubuntu',sans-serif;font-size:9px;color:#1a85c4">Jonathan Doe</div>
  <div style="font-size:7px;color:#333;margin-top:4px">Managing Director XYZ</div>
  <div style="font-family:'PT Serif',serif;font-style:italic;font-size:7px;color:#555;margin-top:3px">Northfield.co.uk</div>
</div>
<p class="abs quote">“Donec sed odio dui. Nulla vitae elit libero, a pharetra augue. Nullam id dolor id nibh ultricies vehicula ut id elit. Integer posuere erat a ante venenatis posuere velit aliquet...”</p>

<footer class="abs footer"></footer>
<div class="abs" style="left:86px;top:1003px;width:102px"><div class="fh">Contact Info</div></div>
<div class="abs flist" style="left:87px;top:1030px">
  <a>lorem ipsum</a><a>dolor sit amet 106</a><a>1404 consecteture</a><a>adipisicing elit</a><a>eMail: info@velkorgroup.com</a><a>Phone: 1-800-555-0142</a>
</div>
<div class="abs" style="left:222px;top:1003px;width:139px"><div class="fh">About Us</div></div>
<p class="abs flist" style="left:222px;top:1030px;width:145px;line-height:14.5px">Lorem ipsum dolor sit amet, consectetur adipisicing elit, sed do eiusmod tempor incididunt ut labore et dolore magna aliqua. Ut enim ad minim veniam.</p>
<div class="abs" style="left:393px;top:1003px;width:102px"><div class="fh">Company Info</div></div>
<div class="abs flist" style="left:394px;top:1029px;line-height:12.6px">
  <a>Home</a><a>Food &amp; Beverage</a><a>Real Estate Development</a><a>Transportation</a><a>Health Care</a><a>Consumer Products Distribution</a><a>Agro Processing</a>
</div>
<div class="abs" style="left:528px;top:1003px;width:176px"><div class="fh">Stay updates on our Socail Network</div></div>
<div class="abs social"><i></i><i></i><i></i></div>
<div class="abs" style="left:528px;top:1070px;width:176px"><div class="fh">Join Our Newsletter</div></div>
<div class="abs newsletter"><span>Enter your email address</span><b>Subscribe</b></div>

<div class="abs footbar">
  <div class="abs" style="left:88px;top:15px">© Copyrights 2014 All rights Reserved</div>
  <div class="abs" style="right:89px;top:15px">Privacy Policy &amp; Terms of uses</div>
</div>
<div class="abs totop"><svg width="14" height="8" viewBox="0 0 14 8" fill="none" stroke="#999" stroke-width="1.5"><path d="M1 7l6-6 6 6"/></svg></div>
</body>
</html>
```